BOLD & MINIMALIST DESIGN NEEDED

We want a very bold but minimalistic business card design that is impactful and utilizes both sides of the business card. Our current logo is included for your use.

We want bold fonts and good use of negative space. We don't want the logo to overpower the design.

Target Market(s)

Professionals who are building new commercial buildings.

Industry/Entity Type

Construction

Contact Information for Business Card

Name, Title, email, office phone, cell phone, website

Font styles to use
Serif
Sans Serif

Requirements
Must have
• Bold design!

```html
<!DOCTYPE html>
<html lang="en">
<head>
<meta charset="UTF-8">
<title>Ridgeline Design + Build — Business Card</title>
<link href="https://fonts.googleapis.com/css2?family=Montserrat:wght@400;600;800&display=swap" rel="stylesheet">
<style>
  :root {
    --backdrop: #949494;
    --ink: #0b0c0e;
    --paper: #ffffff;
    --green: #7dc34f;
    --muted: #7a7a7a;
  }
  * { margin: 0; padding: 0; box-sizing: border-box; }
  html, body { width: 1200px; height: 1200px; overflow: hidden; }
  body {
    background: var(--backdrop);
    font-family: "Montserrat", sans-serif;
    position: relative;
  }
  .card {
    position: absolute;
    left: 179px;
    width: 861px;
    height: 496px;
    overflow: hidden;
  }
  .card--front { top: 84px; background: var(--ink); }
  .card--back { top: 621px; background: var(--paper); }

  /* Front */
  .front-mark {
    position: absolute;
    left: 396px; top: 150px;
    width: 70px; height: 70px;
    background: var(--green);
  }
  .front-name {
    position: absolute;
    left: 0; right: 0; top: 268px;
    text-align: center;
    color: var(--paper);
    font-weight: 800;
  }
  .brand-title { font-size: 50px; line-height: 1; letter-spacing: 1px; }
  .brand-rule {
    width: 346px; height: 2px; margin: 8px auto 4px;
    background: currentColor;
  }
  .brand-sub { font-size: 18px; letter-spacing: 7px; line-height: 1; }

  /* Back */
  .back-brand {
    position: absolute;
    left: 28px; top: 30px;
    width: 360px;
    text-align: center;
    color: var(--ink);
    font-weight: 800;
  }
  .back-brand .brand-title { font-size: 49px; }
  .back-brand .brand-rule { width: 360px; }
  .person {
    position: absolute;
    left: 25px; top: 208px;
  }
  .person-name { font-size: 36px; font-weight: 600; color: var(--ink); line-height: 1.1; letter-spacing: .5px; }
  .person-title { font-size: 29px; font-weight: 400; color: var(--muted); line-height: 1.1; letter-spacing: 1px; }

  .contact-band {
    position: absolute;
    left: 0; top: 300px;
    width: 524px; height: 168px;
    background: var(--ink);
  }
  .contact-list {
    list-style: none;
    position: absolute;
    left: 26px; top: 18px;
  }
  .contact-item {
    display: flex; align-items: center;
    height: 36px;
    color: var(--paper);
    font-size: 24px;
    letter-spacing: 1px;
  }
  .contact-icon { width: 26px; height: 26px; margin-right: 12px; fill: var(--green); }
  .accent-block {
    position: absolute;
    left: 591px; top: 300px;
    width: 168px; height: 168px;
    background: var(--green);
  }
  .band-edge {
    position: absolute;
    left: 826px; top: 300px;
    width: 35px; height: 168px;
    background: var(--ink);
  }
</style>
</head>
<body>
  <section class="card card--front">
    <div class="front-mark"></div>
    <div class="front-name">
      <div class="brand-title">RIDGELINE</div>
      <div class="brand-rule"></div>
      <div class="brand-sub">DESIGN + BUILD</div>
    </div>
  </section>

  <section class="card card--back">
    <div class="back-brand">
      <div class="brand-title">RIDGELINE</div>
      <div class="brand-rule"></div>
      <div class="brand-sub">DESIGN + BUILD</div>
    </div>

    <div class="person">
      <div class="person-name">Name Surename</div>
      <div class="person-title">Director</div>
    </div>

    <div class="contact-band">
      <ul class="contact-list">
        <li class="contact-item">
          <svg class="contact-icon" viewBox="0 0 24 24"><path d="M6.6 10.8a15 15 0 0 0 6.6 6.6l2.2-2.2c.3-.3.7-.4 1-.2 1.1.4 2.3.6 3.6.6.6 0 1 .4 1 1V20c0 .6-.4 1-1 1A17 17 0 0 1 3 4c0-.6.4-1 1-1h3.5c.6 0 1 .4 1 1 0 1.3.2 2.5.6 3.6.1.3 0 .7-.2 1z"/></svg>
          555-014-2200
        </li>
        <li class="contact-item">
          <svg class="contact-icon" viewBox="0 0 24 24"><path d="M2 8c0-2 4-4 10-4s10 2 10 4v2h-5V8H7v2H2z"/><path d="M6 11h12l2 9H4z"/></svg>
          555-014-2200
        </li>
        <li class="contact-item">
          <svg class="contact-icon" viewBox="0 0 24 24"><path d="M2 5h20v14H2z M4 7v.5l8 6 8-6V7z" fill-rule="evenodd"/></svg>
          info@rdb-build.com
        </li>
        <li class="contact-item">
          <svg class="contact-icon" viewBox="0 0 24 24"><path d="M12 2a10 10 0 1 0 0 20 10 10 0 0 0 0-20zm0 2c.9 1 1.7 2.4 2.1 4H9.9C10.3 6.4 11.1 5 12 4zM9.6 10h4.8a13 13 0 0 1 0 4H9.6a13 13 0 0 1 0-4zm-2 0a15 15 0 0 0 0 4H4.3a8 8 0 0 1 0-4zm8.8 0h3.3a8 8 0 0 1 0 4h-3.3a15 15 0 0 0 0-4zM9.9 16h4.2c-.4 1.6-1.2 3-2.1 4-.9-1-1.7-2.4-2.1-4z"/></svg>
          www.rdb-build.com
        </li>
      </ul>
    </div>
    <div class="accent-block"></div>
    <div class="band-edge"></div>
  </section>
</body>
</html>
```